Meridale Hair Studio Needs a new appointment business card

We need a new appointment card for our hair salon.

I Dont want bright out there colours.
I would like it to be neat, clean, easy to read. White, Black, with a hint of colour if needed.

We need
-Logo
-Phone number 47268315
-Mobile Number: 0437608251
Address: Shop 5/213 Tarwin Road, The Crossgate, Kelvindale 4812

BACK SIDE OF CARD
- Appointment Time & Date (White background so we are able to write on it)
(If you are unable to make your appointment please contact us ASAP 47268315)

I also would like the linkpage and Snapframe logo(Find us on Linkpage)(find us on Snapframe)

Target Market(s)

appointment card simple to read. all information for their next appoint For all our clients male and female

Industry/Entity Type

Hairdresser

Contact Information for Business Card

-Logo
-Phone number 47268315

BACK SIDE OF CARD

Font styles to use
Serif
Sans Serif
Script

Requirements
Must have
• White Back ground on backside with appointment deatils so we are able to write information (like appointment time and date)
Nice to have
• Find us on Linkpage
and
snapframe - meridale_hairstudio
Should not have
• BRIGHT COLOURS

```html
<!DOCTYPE html>
<html lang="en">
<head>
<meta charset="utf-8">
<title>Meridale Hair Studio – Appointment Card</title>
<link rel="stylesheet" href="https://fonts.googleapis.com/css2?family=Roboto+Slab:wght@300;400;500&family=Arimo:wght@400;700&display=swap">
<style>
  :root {
    --canvas: #e4e5e7;
    --card-dark: #231f20;
    --card-light: #ffffff;
    --ink: #2b2b2b;
    --ink-soft: #3a3a3a;
    --on-dark: #ffffff;
    --ghost: #f2f2f2;
    --rule: #555555;
    --edge: #8a8a8a;
    --hint-blue: #4a5f9c;
    --hint-rose: #b5567a;
  }
  * { margin: 0; padding: 0; box-sizing: border-box; }
  html, body { width: 1200px; height: 1200px; overflow: hidden; }
  body { background: var(--canvas); position: relative; font-family: "Roboto Slab", Georgia, serif; }

  .card { position: absolute; left: 250px; width: 700px; height: 400px; overflow: hidden; }
  .card--front { top: 190px; background: var(--card-dark); color: var(--on-dark); }
  .card--back { top: 610px; background: var(--card-light); border: 1px solid var(--edge); color: var(--ink); }

  /* Front */
  .brand { position: absolute; left: 56px; top: 184px; }
  .brand__name { font-weight: 400; font-size: 33px; letter-spacing: 1px; line-height: 1; }
  .brand__sub { font-family: "Arimo", Arial, sans-serif; font-size: 11px; margin-top: 5px; margin-left: 48px; }
  .divider { position: absolute; left: 307px; top: 108px; width: 2px; height: 183px; background: var(--on-dark); }
  .contact { list-style: none; font-size: 15.5px; font-weight: 400; }
  .contact__item { position: absolute; left: 360px; display: flex; align-items: flex-start; }
  .contact__item--phone { top: 141px; }
  .contact__item--mobile { top: 177px; }
  .contact__item--address { top: 207px; }
  .contact__icon { width: 16px; height: 20px; margin-right: 18px; margin-top: 3px; flex: none; }
  .contact__text { line-height: 27px; }

  /* Back */
  .ghost-mark { position: absolute; left: 24px; top: 62px; color: var(--ghost); line-height: 1; pointer-events: none; }
  .ghost-mark__sub { font-family: "Arimo", Arial, sans-serif; font-size: 34px; margin-left: 94px; }
  .ghost-mark__name { font-weight: 300; font-size: 96px; letter-spacing: 14px; margin-top: -2px; }

  .appointment__title { position: absolute; left: 0; right: 0; top: 146px; text-align: center; font-size: 25px; font-weight: 400; color: var(--ink); }
  .field { position: absolute; display: flex; align-items: flex-end; font-family: "Arimo", Arial, sans-serif; }
  .field--date { left: 205px; top: 218px; }
  .field--time { left: 205px; top: 266px; }
  .field__label { font-weight: 700; font-size: 19px; color: var(--ink-soft); width: 78px; }
  .field__line { width: 155px; border-bottom: 1px solid var(--rule); margin-bottom: 3px; }
  .field--time .field__line { margin-left: -2px; }
  .field__suffix { font-weight: 700; font-size: 10px; text-decoration: underline; margin-left: 22px; color: var(--ink-soft); }

  .social { position: absolute; left: 0; right: 0; top: 322px; display: flex; justify-content: center; gap: 30px; list-style: none; font-size: 13px; color: var(--ink); }
  .social__item { display: flex; align-items: center; gap: 8px; }
  .social__dot { width: 30px; height: 30px; border-radius: 50%; }
  .social__dot--link { background: var(--hint-blue); }
  .social__dot--snap { background: var(--hint-rose); }
</style>
</head>
<body>

<section class="card card--front" aria-label="Front of appointment card">
  <div class="brand">
    <div class="brand__name">MERIDALE</div>
    <div class="brand__sub">HAIR-STUDIO</div>
  </div>
  <div class="divider"></div>
  <ul class="contact">
    <li class="contact__item contact__item--phone">
      <svg class="contact__icon" viewBox="0 0 16 20" aria-hidden="true"><path d="M4 1 L7 5 L5 7.5 C6 10.5 8 13 10.5 14.5 L13 12.5 L15.5 16 L13 18.5 C7 17.5 2 11 1.5 3.5 Z" fill="#fff"/></svg>
      <span class="contact__text">47268315</span>
    </li>
    <li class="contact__item contact__item--mobile">
      <svg class="contact__icon" viewBox="0 0 16 20" aria-hidden="true"><rect x="3" y="1" width="10" height="18" rx="1.5" fill="none" stroke="#fff" stroke-width="2"/></svg>
      <span class="contact__text">0437608251</span>
    </li>
    <li class="contact__item contact__item--address">
      <svg class="contact__icon" viewBox="0 0 16 20" aria-hidden="true"><path d="M8 1.5 C4.5 1.5 2.5 4 2.5 6.8 C2.5 10 8 15 8 15 C8 15 13.5 10 13.5 6.8 C13.5 4 11.5 1.5 8 1.5 Z" fill="none" stroke="#fff" stroke-width="2"/><circle cx="8" cy="7" r="2" fill="#fff"/><rect x="2" y="17" width="12" height="2" fill="#fff"/></svg>
      <span class="contact__text">Shop 5/213 Tarwin Road,<br>The Crossgate, Kelvindale 4812</span>
    </li>
  </ul>
</section>

<section class="card card--back" aria-label="Back of appointment card">
  <div class="ghost-mark" aria-hidden="true">
    <div class="ghost-mark__sub">HAIR-STUDIO</div>
    <div class="ghost-mark__name">MERIDALE</div>
  </div>
  <h2 class="appointment__title">YOUR NEXT APPOINTMENT IS</h2>
  <div class="field field--date">
    <span class="field__label">DATE:</span>
    <span class="field__line"></span>
  </div>
  <div class="field field--time">
    <span class="field__label">TIME:</span>
    <span class="field__line"></span>
    <span class="field__suffix">AM/PM</span>
  </div>
  <ul class="social">
    <li class="social__item"><span class="social__dot social__dot--link"></span>Linkpage</li>
    <li class="social__item"><span class="social__dot social__dot--snap"></span>Snapframe</li>
  </ul>
</section>

</body>
</html>
```